Business Card Design

Business Card for professional consulting firm working with large financial institutions.

Target Market(s)

Executive buyers

Industry/Entity Type

Banking

Contact Information for Business Card

Mild creativity wanted. Not boring, but do elaborate artwork.

Font styles to use
Serif
Sans Serif

Colors

Designer to choose colors to be used in the design.

Requirements
Must have
• Standard business card features - company name, individual name, telephone, website, email, locations.
Nice to have
• Two colors
Should not have
• too many colors, fancy printing, cartoons.

```html
<!DOCTYPE html>
<html lang="en">
<head>
<meta charset="utf-8">
<title>Northvale Business Card</title>
<link rel="stylesheet" href="https://fonts.googleapis.com/css2?family=Lato:wght@400;700&display=swap">
<style>
  :root {
    --brand-blue: #0a2f8f;
    --swoosh-grey: #c4c4c4;
    --card-white: #ffffff;
    --ink-dark: #2a2a2a;
    --stage: #e9eaec;
  }
  * { box-sizing: border-box; margin: 0; padding: 0; }
  html, body { width: 1200px; height: 782px; overflow: hidden; }
  body {
    background: var(--stage);
    font-family: "Lato", Arial, sans-serif;
    display: flex;
    align-items: center;
    justify-content: center;
    gap: 50px;
  }
  .card {
    position: relative;
    width: 520px;
    height: 298px;
    overflow: hidden;
    box-shadow: 0 6px 18px rgba(0,0,0,.18);
  }
  .card--back { background: var(--brand-blue); color: var(--card-white); }
  .card--front { background: var(--card-white); }

  .brand-name {
    position: absolute;
    font-family: "Lato", Arial, sans-serif;
    font-weight: 400;
    font-size: 44px;
    letter-spacing: 1px;
  }
  .card--back .brand-name { left: 0; right: 0; top: 100px; text-align: center; color: var(--card-white); }
  .card--front .brand-name { left: 250px; top: 126px; color: var(--brand-blue); font-size: 38px; }

  .website {
    position: absolute;
    font-size: 15px;
    letter-spacing: .5px;
  }
  .card--back .website { left: 0; right: 0; top: 210px; text-align: center; }
  .card--front .website { right: 40px; bottom: 24px; color: var(--card-white); }

  .wave { position: absolute; inset: 0; width: 100%; height: 100%; }
  .wave__band { fill: var(--brand-blue); }
  .wave__swoosh { fill: var(--swoosh-grey); }

  .person { position: absolute; left: 30px; top: 26px; }
  .person__name { color: var(--brand-blue); font-size: 17px; font-weight: 400; letter-spacing: .5px; }
  .person__title { color: var(--ink-dark); font-size: 12px; margin-top: 1px; }

  .contact { position: absolute; left: 30px; top: 96px; list-style: none; color: var(--ink-dark); font-size: 13px; line-height: 18px; }
  .contact li { display: flex; align-items: center; gap: 5px; }
  .contact svg { width: 11px; height: 11px; fill: var(--brand-blue); }
  .contact .address { display: block; margin-top: 2px; }
</style>
</head>
<body>
  <section class="card card--back" aria-label="Card back">
    <div class="brand-name">Northvale</div>
    <div class="website">www.northvale.com</div>
  </section>

  <section class="card card--front" aria-label="Card front">
    <svg class="wave" viewBox="0 0 520 298" preserveAspectRatio="none" aria-hidden="true">
      <path class="wave__swoosh" d="M0,148 C110,198 220,204 320,211 C420,219 480,234 520,262 L520,280 C470,250 400,235 300,225 C200,215 120,210 0,166 Z"/>
      <path class="wave__band" d="M0,166 C120,210 200,215 300,225 C400,235 470,250 520,280 L520,298 L0,298 Z"/>
    </svg>

    <div class="person">
      <div class="person__name">DANIEL CARTER</div>
      <div class="person__title">Managing Director</div>
    </div>

    <ul class="contact">
      <li><svg viewBox="0 0 24 24"><path d="M6.6 10.8a15 15 0 0 0 6.6 6.6l2.2-2.2c.3-.3.7-.4 1-.2 1.1.4 2.3.6 3.6.6.6 0 1 .4 1 1V20c0 .6-.4 1-1 1A17 17 0 0 1 3 4c0-.6.4-1 1-1h3.5c.6 0 1 .4 1 1 0 1.3.2 2.5.6 3.6.1.3 0 .7-.2 1z"/></svg>044-987 654 321</li>
      <li><svg viewBox="0 0 24 24"><path d="M2 5h20v14H2z M2 5l10 8 10-8" /></svg>hello@northvale.com</li>
      <li class="address">48 Harbour Street<br>Dublin, 100482</li>
    </ul>

    <div class="brand-name">Northvale</div>
    <div class="website">www.northvale.com</div>
  </section>
</body>
</html>
```